Flyer for spiritual retreat (yoga, meditation, reiki, raw food)

I would like a flyer to promote my upcoming retreat and a matching Facebook banner.

The name of the retreat is "OutBloom the Spirit" and the tagline is "retreat into you"

The activities in the retreat include daily meditation, ecstatic dance, spiritual development workshops on intuition, energy healing etc and a reiki session is included.

I would like a flyer designed to promote this, something that is editable as I will be running this multiple times and will need to adjust the flyer to add the dates etc each time.

edit: add that here will be fully catered raw food and juices, and that the retreat price includes all accomodation, meals and workshops.

Please contact me if you need further info. Please also visit my website www.marlavosk.com and www.pagenest.com/koruhaven to see my current events and promotions.

Thank you,

Marla

Reason: Hi all, thank you all for your submissions. Apologies as I am traveling and do not have much access to internet and will review your submissions and provide feedback as soon as possible. Kind regards, Marla.

Target Market(s)

People who like meditation, yoga, fans of tomas brenner and wendell marsh, those interested in personal and spiritual development.

Industry/Entity Type

Health And Wellness

Requirements
Must have
• Please put the included reiki session as as added bonus. Something like "BONUS 30 minute reiki healing session" in a little star/banner/something that stands out.
• Please emphasise the "light" part of OutBloom as I am going for a play on words between in the light and enlightenment.
• Please include placeholder text for place, location, time
• Placeholder for price
• My name (see attached file - can change colour to suit) and website (www.marlavosk.com)
Nice to have
• I prefer rounded designs, curves rather than block designs.
Should not have
• Koru Haven logo

```html
<!DOCTYPE html>
<html lang="en">
<head>
<meta charset="utf-8">
<title>OutBloom the Spirit – Retreat Into You</title>
<link rel="stylesheet" href="https://fonts.googleapis.com/css2?family=Poppins:wght@500;600;700&family=Montserrat:ital,wght@1,800&family=Oswald:wght@400;500;600&family=Great+Vibes&display=swap">
<style>
  :root {
    --navy: #2b3a8f;
    --sky: #1aa3e0;
    --ink: #1b1b1d;
    --paper: #ffffff;
    --mist: #eef0f2;
  }
  * { box-sizing: border-box; margin: 0; padding: 0; }
  html, body { width: 848px; height: 1200px; overflow: hidden; background: var(--paper); }
  .flyer { position: relative; width: 848px; height: 1200px; overflow: hidden; background: var(--paper); font-family: "Poppins", sans-serif; }
  .backdrop { position: absolute; inset: 0; }

  .host-name {
    position: absolute; left: 420px; top: 118px;
    font-family: "Great Vibes", cursive; font-size: 76px; line-height: 1;
    color: var(--mist); transform: rotate(-8deg); transform-origin: left center;
    text-shadow: 0 0 2px #6d7078, 1px 1px 0 #6d7078, -1px -1px 0 #6d7078;
    white-space: nowrap;
  }

  .bonus-badge {
    position: absolute; left: 612px; top: 330px; width: 180px; height: 180px;
    border-radius: 50%; background: var(--navy); border: 5px solid var(--paper);
    display: flex; flex-direction: column; align-items: center; justify-content: center;
    text-align: center; color: var(--paper); font-family: "Oswald", sans-serif;
    box-shadow: 0 0 0 4px var(--sky);
  }
  .bonus-badge .bonus-label { font-size: 34px; font-weight: 600; line-height: 1; letter-spacing: 2px; color: var(--sky); }
  .bonus-badge .bonus-text { font-size: 19px; font-weight: 500; line-height: 23px; margin-top: 6px; }

  .title { position: absolute; inset: 0; pointer-events: none; }
  .title span { position: absolute; line-height: 1; white-space: nowrap;
    text-shadow: 0 0 3px var(--paper), 0 0 3px var(--paper), 0 0 3px var(--paper); }
  .title-lead { left: 312px; top: 612px; font-size: 72px; font-weight: 700; color: var(--navy); }
  .title-key { left: 300px; top: 665px; font-size: 158px; font-weight: 700; color: var(--navy); letter-spacing: -4px; }
  .title-key .soft { color: var(--sky); font-weight: 600; }
  .title-joiner { left: 345px; top: 808px; font-size: 80px; font-weight: 500; color: var(--sky); }
  .title-end { right: 26px; top: 772px; font-size: 128px; font-weight: 600; color: var(--sky); letter-spacing: -3px; }

  .tagline-rule { position: absolute; height: 5px; background: var(--ink); }
  .tagline-rule.top { left: 185px; top: 922px; width: 530px; }
  .tagline-rule.bottom { left: 726px; top: 1000px; width: 122px; }
  .tagline {
    position: absolute; left: 132px; top: 934px;
    font-family: "Montserrat", sans-serif; font-style: italic; font-weight: 800;
    font-size: 54px; line-height: 1; color: var(--ink); letter-spacing: 0.5px;
  }

  .activities {
    position: absolute; left: 0; right: 0; top: 1012px; text-align: center;
    font-family: "Oswald", sans-serif; font-weight: 400; font-size: 27px;
    line-height: 34px; color: var(--ink); letter-spacing: 0.4px;
  }
  .event-details {
    position: absolute; left: 0; right: 0; top: 1086px; text-align: center;
    font-family: "Oswald", sans-serif; font-weight: 500; font-size: 18px;
    line-height: 24px; color: var(--navy); letter-spacing: 0.6px;
  }

  .footer-line { position: absolute; left: 0; right: 0; top: 1124px; height: 7px; background: var(--sky); }
  .footer-base { position: absolute; left: 0; right: 0; top: 1176px; height: 24px; background: var(--ink); }
  .contact {
    position: absolute; top: 1142px; display: flex; align-items: center; gap: 8px;
    font-family: "Oswald", sans-serif; font-weight: 500; font-size: 22px; color: var(--ink);
  }
  .contact.site { left: 28px; }
  .contact.social { right: 26px; }
  .contact .dot { width: 20px; height: 20px; border-radius: 50%; background: var(--ink); }
</style>
</head>
<body>
<main class="flyer">
  <svg class="backdrop" width="848" height="1200" viewBox="0 0 848 1200">
    <defs>
      <linearGradient id="garden-tones" x1="0" y1="0" x2="0" y2="1">
        <stop offset="0" stop-color="#7fa36a"/>
        <stop offset="0.3" stop-color="#5d7f4c"/>
        <stop offset="0.42" stop-color="#a9a49b"/>
        <stop offset="1" stop-color="#c4bdb4"/>
      </linearGradient>
    </defs>
    <rect class="hero-photo" x="0" y="0" width="848" height="900" fill="url(#garden-tones)"
          role="img" aria-label="Photo of the host sitting barefoot on a large rose quartz stone in a gravel garden, arms raised joyfully"/>

    <path class="top-band" d="M0,0 H848 V48 C690,112 500,168 330,160 C190,152 80,118 0,90 Z" fill="var(--sky)"/>
    <path class="top-cap" d="M0,0 H848 V14 C690,70 500,124 330,120 C200,116 90,86 0,58 Z" fill="var(--paper)"/>
    <path class="top-stroke" d="M280,66 C460,72 660,38 848,0 V12 C660,58 460,84 280,66 Z" fill="var(--ink)"/>

    <path class="bottom-band" d="M0,860 C220,745 520,640 848,600 V1200 H0 Z" fill="var(--sky)"/>
    <path class="bottom-stroke" d="M170,722 C380,660 620,622 848,612 V630 C620,642 400,676 170,722 Z" fill="var(--ink)"/>
    <path class="bottom-panel" d="M0,905 C220,790 520,690 848,655 V1200 H0 Z" fill="var(--paper)"/>
  </svg>

  <div class="host-name">Marla Vosk</div>

  <div class="bonus-badge">
    <span class="bonus-label">BONUS</span>
    <span class="bonus-text">30 MINUTE<br>REIKI HEALING<br>SESSION</span>
  </div>

  <h1 class="title" aria-label="OutBloom the Spirit">
    <span class="title-lead">Out</span>
    <span class="title-key">Blo<span class="soft">om</span></span>
    <span class="title-joiner">the</span>
    <span class="title-end">Spirit</span>
  </h1>

  <div class="tagline-rule top"></div>
  <p class="tagline">RETREAT INTO YOU</p>
  <div class="tagline-rule bottom"></div>

  <p class="activities">DAILY MEDITATION, ECSTATIC DANCE,<br>SPIRITUAL DEVELOPMENT WORKSHOPS ON INTUITION</p>
  <p class="event-details">DATE: DD/MM/YYYY &nbsp;•&nbsp; TIME: 00:00 &nbsp;•&nbsp; PLACE: VENUE, CITY &nbsp;•&nbsp; PRICE: $000</p>

  <div class="footer-line"></div>
  <p class="contact site"><span class="dot"></span>WWW.MARLAVOSK.COM</p>
  <p class="contact social"><span class="dot"></span>WWW.PAGENEST.COM/KORUHAVEN</p>
  <div class="footer-base"></div>
</main>
</body>
</html>
```